Healthy lifestyle Influencer business card

I need your creativity to have a business card that I can leave in all the restaurants, hotels and spas I visit to inform them that I am an influencer specializing in the wellness sector and that I will write a review about them. You can use my instagram photos Lunavita27 or on my website www.piattileggeriorto.it. I would like my business card to impress with its creativity! thank you very much!

Contact Information for Business Card

siteweb, instagram, phone number

Font styles to use
Decorative
Script

Colors
0094D4
00A9DD
6FCCEA
C7EBF8
E9F6FB
59FF00
82FF00
B8FF75
E3FFCB
F4FFEA
FFC000
F8CF3A
FAE287
FDF2CF
FEFAEE
F0912C
F2A743
F7CA91
FBE8D2
FDF5EE
EE7325
F08F49
F5BC92
FAE3D3
FDF4ED
EB3D1F
EC4F4E
F09395
F8D3D4
FCEDEE
E54698
E96AAD
F1A4CE
F9D9EA
FCEFF6

Requirements
Nice to have
• creativity

```html
<!DOCTYPE html>
<html lang="it">
<head>
<meta charset="utf-8">
<title>Luna Vita Chef – Biglietto da visita</title>
<link rel="stylesheet" href="https://fonts.googleapis.com/css2?family=Alex+Brush&family=Jost:wght@400&family=Roboto:wght@300;400&display=swap">
<style>
  :root{
    --stage:#2b2b2b;
    --sage:#86b8aa;
    --sage-deep:#74a898;
    --sage-light:#a3cabf;
    --paper:#f2f2f1;
    --paper-shade:#e6e7e6;
    --ink:#3d3d3d;
    --ink-soft:#555;
    --icon:#8fa9a2;
    --band:#4a4a4a;
    --band-text:#e8e8e8;
  }
  *{margin:0;padding:0;box-sizing:border-box}
  html,body{width:1200px;height:1138px;overflow:hidden;background:var(--stage)}
  .card{position:absolute;left:273px;width:622px;height:376px;border-radius:16px;overflow:hidden}
  .card--front{top:184px}
  .card--back{top:606px;background:linear-gradient(180deg,var(--paper) 0%,var(--paper-shade) 100%)}

  .food-grid{position:absolute;inset:0;background:radial-gradient(ellipse at 50% 45%,var(--sage-light) 0%,var(--sage) 55%,var(--sage-deep) 100%)}

  .brand-name{font-family:"Jost",sans-serif;font-weight:400;color:var(--ink);white-space:nowrap;letter-spacing:.5px}
  .tagline{font-family:"Jost",sans-serif;font-weight:400;color:var(--ink);white-space:nowrap}

  .card--front .brand-name{position:absolute;left:0;right:0;top:146px;text-align:center;font-size:44px}
  .card--front .tagline{position:absolute;left:0;right:0;top:210px;text-align:center;font-size:20px}

  .social{position:absolute;display:flex;align-items:center;gap:10px;font-family:"Roboto",sans-serif;font-weight:300;white-space:nowrap}
  .social__dot{width:15px;height:15px;border-radius:50%}
  .card--front .social{left:0;right:0;top:328px;justify-content:center;font-size:17px;color:var(--ink)}
  .card--front .social__dot{background:var(--ink)}

  .card--back .brand-name{position:absolute;left:30px;width:290px;top:152px;text-align:center;font-size:38px}
  .card--back .tagline{position:absolute;left:30px;width:290px;top:203px;text-align:center;font-size:16px}

  .person-name{position:absolute;left:358px;top:106px;font-family:"Alex Brush",cursive;font-size:34px;color:var(--ink);white-space:nowrap}
  .contacts{position:absolute;left:372px;top:156px;list-style:none;font-family:"Roboto",sans-serif;font-weight:300;font-size:17px;color:var(--ink-soft)}
  .contacts li{display:flex;align-items:center;gap:11px;height:24px;white-space:nowrap}
  .contacts svg{width:15px;height:13px;fill:none;stroke:var(--icon);stroke-width:1.4}
  .vat{position:absolute;left:369px;top:235px;font-family:"Roboto",sans-serif;font-weight:300;font-size:17px;color:var(--ink-soft);white-space:nowrap}

  .accent-strip{position:absolute;left:0;bottom:0;width:290px;height:13px;background:var(--sage)}
  .footer-band{position:absolute;right:0;bottom:0;width:352px;height:46px;background:var(--band);clip-path:polygon(8% 0,100% 0,100% 100%,0 100%)}
  .card--back .social{left:438px;bottom:13px;font-size:17px;color:var(--band-text)}
  .card--back .social__dot{background:var(--band-text)}
</style>
</head>
<body>
  <section class="card card--front">
    <div class="food-grid" role="img" aria-label="Griglia di foto di piatti sani e leggeri, velata in verde salvia"></div>
    <div class="brand-name">Luna Vita Chef</div>
    <div class="tagline">Il gusto sano che ti fa bene</div>
    <div class="social"><span class="social__dot"></span>@Lunavita27</div>
  </section>

  <section class="card card--back">
    <div class="brand-name">Luna Vita Chef</div>
    <div class="tagline">Il gusto sano che ti fa bene</div>

    <div class="person-name">Luna Ferraris</div>
    <ul class="contacts">
      <li><svg viewBox="0 0 15 13"><path d="M2 5c0-2 3-3 5.5-3S13 3 13 5l-2 .5L10 4H5L4 5.5Z"/><rect x="3" y="6.5" width="9" height="5" rx="1"/></svg>000-0000-0000</li>
      <li><svg viewBox="0 0 15 13"><rect x="1" y="2" width="13" height="9"/><path d="M1 2l6.5 5L14 2"/></svg>info@piattileggeriorto.it</li>
      <li><svg viewBox="0 0 15 13"><circle cx="7.5" cy="6.5" r="5.5"/><ellipse cx="7.5" cy="6.5" rx="2.3" ry="5.5"/><path d="M2 6.5h11"/></svg>www.piattileggeriorto.it</li>
    </ul>
    <div class="vat">Partita IVA 01234560789</div>

    <div class="accent-strip"></div>
    <div class="footer-band"></div>
    <div class="social"><span class="social__dot"></span>@Lunavita27</div>
  </section>
</body>
</html>
```